Structural Engineering Business Card

Brookvane Drafting does residential house plans for clients in Central Florida. Would like simple but elegant business card that is appropriate for a house plan engineering company. Prefer black business card with black/white them but open to other shades of blue. I uploaded a sample card that I came across that looked good but please come up with your own creative designs.

Contact Information for Business Card

Name, Title, Phone, Email, Address, website

```html
<!DOCTYPE html>
<html lang="en">
<head>
<meta charset="utf-8">
<title>Brookvane Drafting – Business Card</title>
<link rel="stylesheet" href="https://fonts.googleapis.com/css2?family=Lato:wght@400;700;900&display=swap">
<style>
  :root {
    --page: #e9e7e4;
    --card-dark: #141414;
    --card-dark-tint: #262626;
    --card-light: #ffffff;
    --card-light-tint: #eeeeee;
    --ink: #111111;
    --ink-soft: #333333;
    --paper: #ffffff;
  }
  * { box-sizing: border-box; margin: 0; padding: 0; }
  html, body { width: 1200px; height: 992px; overflow: hidden; }
  body {
    background: var(--page);
    font-family: "Lato", sans-serif;
    color: var(--ink);
    display: flex;
    flex-direction: column;
    align-items: center;
    justify-content: center;
    gap: 56px;
  }
  .card {
    position: relative;
    width: 660px;
    height: 377px;
    border-radius: 22px;
    overflow: hidden;
    box-shadow: 0 10px 28px rgba(0,0,0,.22);
  }
  .card__drawing { position: absolute; inset: 0; }

  /* Front */
  .card--front { background: var(--card-dark); }
  .card--front .card__drawing {
    background: radial-gradient(ellipse at 70% 70%, var(--card-dark-tint) 0%, var(--card-dark) 70%);
  }
  .card--front .wordmark {
    position: absolute;
    left: 0; right: 0; top: 50%;
    transform: translateY(-50%);
    text-align: center;
    color: var(--paper);
    font-weight: 900;
    font-size: 50px;
    letter-spacing: 1px;
    text-transform: uppercase;
    line-height: 1.05;
  }

  /* Back */
  .card--back { background: var(--card-light); }
  .card--back .card__drawing {
    background: radial-gradient(ellipse at 72% 75%, var(--card-light-tint) 0%, var(--card-light) 70%);
  }
  .card__body {
    position: relative;
    display: flex;
    align-items: center;
    height: 100%;
    padding: 0 40px;
  }
  .card--back .wordmark {
    width: 250px;
    font-weight: 900;
    font-size: 32px;
    line-height: 1.08;
    text-transform: uppercase;
    color: var(--ink);
  }
  .divider {
    width: 2px;
    height: 170px;
    background: var(--ink);
    margin: 40px 30px 0 28px;
    align-self: flex-start;
    margin-top: 150px;
  }
  .contact { margin-top: 120px; }
  .contact__name {
    font-weight: 900;
    font-size: 27px;
    letter-spacing: 1px;
    text-transform: uppercase;
  }
  .contact__title { font-size: 18px; color: var(--ink-soft); margin-bottom: 10px; }
  .contact__list { list-style: none; }
  .contact__item {
    display: flex;
    align-items: flex-start;
    gap: 10px;
    font-size: 15px;
    line-height: 1.3;
    margin-bottom: 5px;
    color: var(--ink-soft);
  }
  .contact__item--phone { font-size: 18px; font-weight: 700; color: var(--ink); }
  .contact__item svg { width: 15px; height: 15px; flex: none; margin-top: 2px; fill: var(--ink); }
</style>
</head>
<body>

  <section class="card card--front" aria-label="Card front">
    <div class="card__drawing" role="img" aria-label="Faint architectural elevation drawing of a house on a grid"></div>
    <div class="wordmark">Brookvane<br>Drafting</div>
  </section>

  <section class="card card--back" aria-label="Card back">
    <div class="card__drawing" role="img" aria-label="Faint architectural elevation drawing of a house on a grid"></div>
    <div class="card__body">
      <div class="wordmark">Brookvane<br>Drafting</div>
      <div class="divider"></div>
      <div class="contact">
        <h1 class="contact__name">Daniel Reyes</h1>
        <p class="contact__title">Founder &amp; CEO</p>
        <ul class="contact__list">
          <li class="contact__item">
            <svg viewBox="0 0 24 24" aria-hidden="true"><path d="M12 2a7 7 0 0 0-7 7c0 5 7 13 7 13s7-8 7-13a7 7 0 0 0-7-7zm0 9.5A2.5 2.5 0 1 1 12 6.5a2.5 2.5 0 0 1 0 5z"/></svg>
            <span>Your Address, City<br>State, Zip 1235</span>
          </li>
          <li class="contact__item contact__item--phone">
            <svg viewBox="0 0 24 24" aria-hidden="true"><path d="M6.6 10.8a15.1 15.1 0 0 0 6.6 6.6l2.2-2.2a1 1 0 0 1 1-.25 11.4 11.4 0 0 0 3.6.57 1 1 0 0 1 1 1V20a1 1 0 0 1-1 1A17 17 0 0 1 3 4a1 1 0 0 1 1-1h3.5a1 1 0 0 1 1 1c0 1.25.2 2.45.57 3.57a1 1 0 0 1-.25 1z"/></svg>
            <span>(123) 456-7890</span>
          </li>
          <li class="contact__item">
            <svg viewBox="0 0 24 24" aria-hidden="true"><path d="M2 5h20v14H2zm2 2v.5l8 5 8-5V7l-8 5z"/></svg>
            <span>office@brookvane.com</span>
          </li>
          <li class="contact__item">
            <svg viewBox="0 0 24 24" aria-hidden="true"><path d="M12 2a10 10 0 1 0 0 20 10 10 0 0 0 0-20zm6.9 9h-3a15 15 0 0 0-1.2-5.3A8 8 0 0 1 18.9 11zM12 4.1c.9 1.3 1.7 3.6 1.9 6.9h-3.8c.2-3.3 1-5.6 1.9-6.9zM9.3 5.7A15 15 0 0 0 8.1 11h-3a8 8 0 0 1 4.2-5.3zM5.1 13h3a15 15 0 0 0 1.2 5.3A8 8 0 0 1 5.1 13zm6.9 6.9c-.9-1.3-1.7-3.6-1.9-6.9h3.8c-.2 3.3-1 5.6-1.9 6.9zm2.7-1.6a15 15 0 0 0 1.2-5.3h3a8 8 0 0 1-4.2 5.3z"/></svg>
            <span>www.brookvane.com</span>
          </li>
        </ul>
      </div>
    </div>
  </section>

</body>
</html>
```